Upmarket Dessert Lounge needs a Business Card Design

We are an upmarket dessert lounge needing a business card to match our image.

We want something that is simple yet beautiful, feminine, classy, sophisticated and elegant. We want it to stand out and don't mind if it is bold.

The design should include our logo and colours of red or maroon with gold highlights. We don't mind if black is used.

Marlow & Quince

Target Market(s)

For those who like to indulge or treat themselves and give in to their temptations on good quality desserts.

Industry/Entity Type

Business

Requirements
Must have
• Must include our logo and our name

Marlow & Quince

M & Q

```html
<!DOCTYPE html>
<html lang="en">
<head>
<meta charset="utf-8">
<title>Marlow &amp; Quince — Business Card</title>
<link rel="stylesheet" href="https://fonts.googleapis.com/css2?family=Cinzel:wght@400;600&family=Open+Sans:wght@400;600&display=swap">
<style>
  :root {
    --maroon: #6b1a1c;
    --gold: #d9a86c;
    --gold-glow: rgba(217, 168, 108, 0.5);
    --gold-clear: rgba(217, 168, 108, 0);
    --peach: #f3c894;
    --paper: #ffffff;
    --backdrop: #f2e3e4;
    --ink-light: #ffffff;
  }
  * { box-sizing: border-box; margin: 0; padding: 0; }
  html, body { width: 1200px; height: 951px; overflow: hidden; }
  body {
    background: var(--backdrop);
    font-family: "Open Sans", Arial, sans-serif;
    position: relative;
  }
  .card {
    position: absolute;
    width: 620px;
    height: 354px;
    border-radius: 22px;
    overflow: hidden;
    box-shadow: 0 10px 26px rgba(80, 20, 25, 0.22);
  }
  .card-front {
    left: 110px;
    top: 80px;
    background: var(--maroon);
  }
  .card-back {
    left: 470px;
    top: 500px;
    background: var(--paper);
  }
  .corner-flourish {
    position: absolute;
    top: 0;
    right: 0;
    width: 260px;
    height: 150px;
    background: radial-gradient(ellipse closest-side at 62% 30%, var(--gold-glow), var(--gold-clear));
  }
  .front-wordmark {
    position: absolute;
    left: 40px;
    top: 140px;
    width: 380px;
    text-align: center;
    font-family: "Cinzel", Georgia, serif;
    font-weight: 400;
    font-size: 32px;
    letter-spacing: 1px;
    color: var(--gold);
  }
  .front-web {
    position: absolute;
    left: 0;
    width: 460px;
    top: 288px;
    text-align: center;
    font-size: 17px;
    letter-spacing: 1.5px;
    color: var(--ink-light);
  }
  .back-shape {
    position: absolute;
    inset: 0;
    width: 620px;
    height: 354px;
  }
  .back-monogram {
    position: absolute;
    left: 22px;
    top: 70px;
    width: 170px;
    text-align: center;
    font-family: "Cinzel", Georgia, serif;
    font-weight: 400;
    font-size: 42px;
    white-space: nowrap;
    color: var(--maroon);
  }
  .back-name {
    position: absolute;
    left: 34px;
    top: 204px;
    font-size: 20px;
    white-space: nowrap;
    color: var(--maroon);
  }
  .back-details {
    position: absolute;
    right: 40px;
    text-align: right;
    font-size: 16px;
    line-height: 1.3;
    font-style: normal;
    color: var(--ink-light);
  }
  .back-address { top: 120px; }
  .back-contact { top: 215px; }
</style>
</head>
<body>
  <section class="card card-front" aria-label="Business card front">
    <div class="corner-flourish" role="img" aria-label="Gold floral flourish ornament"></div>
    <p class="front-wordmark">Marlow &amp; Quince</p>
    <p class="front-web">www.marlowquince.com</p>
  </section>

  <section class="card card-back" aria-label="Business card back">
    <svg class="back-shape" viewBox="0 0 620 354" aria-hidden="true">
      <path d="M226 0 C176 120 286 230 236 354 L620 354 L620 0 Z" fill="var(--peach)"/>
      <path d="M242 0 C192 120 302 230 252 354 L620 354 L620 0 Z" fill="var(--maroon)"/>
    </svg>
    <div class="corner-flourish" role="img" aria-label="Gold floral flourish ornament"></div>
    <p class="back-monogram">M &amp; Q</p>
    <p class="back-name">Marlow &amp; Quince</p>
    <address class="back-details back-address">
      1480 Linden Park Rd.<br>
      Suite 204-310<br>
      Harlow, TX 78114
    </address>
    <p class="back-details back-contact">
      555-014-2290<br>
      555-014-2291<br>
      info@marlowquince.com<br>
      www.marlowquince.com
    </p>
  </section>
</body>
</html>
```